New web design for a service provider in the medical field

We are looking for a new design for our website. We are a company that repairs and sells medical endoscopes. Our customers include doctors and hospitals. Our current website can be found at https://lumavex.de/en/lumavex-english.
We need a new web design (without programming) for the following 3 pages:
-Startpage https://lumavex.de/en/lumavex-english/
-Used endoscopes https://lumavex.de/en/used-endoscopes/
-Purchase https://lumavex.de/en/purchase/
The design should be modern and stylish.
The blue color of the logo should be reflected on the page, but not too intrusive.
I have uploaded the images from the header. If more images are needed, let me know and I will upload them.

Target Market(s)
Doctors and hospitals

```html
<!DOCTYPE html>
<html lang="en">
<head>
<meta charset="utf-8">
<title>Lumavex – Sell Your Endoscope</title>
<link href="https://fonts.googleapis.com/css2?family=Barlow:wght@500;600;700&family=Roboto:wght@400;500&display=swap" rel="stylesheet">
<style>
:root{
  --blue:#0a76bd;
  --sky:#27a9e1;
  --ink:#333a40;
  --text:#4a5058;
  --line:#4a9fd6;
  --bg-top:#eef6fa;
  --bg-mid:#dff1f8;
  --navy:#021f3a;
  --white:#ffffff;
}
*{box-sizing:border-box;margin:0;padding:0}
html,body{width:1200px;height:2257px;overflow:hidden}
body{font-family:"Roboto",sans-serif;color:var(--text);background:var(--white)}
.page{position:relative;width:1200px;height:2257px;overflow:hidden;
  background:linear-gradient(180deg,var(--bg-top) 0,#e8f4f9 500px,var(--bg-mid) 1300px,#e9f5fa 1882px,var(--white) 1882px)}
.abs{position:absolute}
h1,h2,h3,h4{font-family:"Barlow",sans-serif;color:var(--ink)}
.accent{color:var(--sky)}

/* top bar */
.topbar{left:156px;top:12px;width:888px;height:20px;display:flex;align-items:center;font-size:11px;color:var(--ink)}
.topbar .contact{display:flex;gap:24px}
.topbar .item{display:flex;align-items:center;gap:7px}
.topbar .links{margin-left:auto;display:flex;gap:28px}
.topbar .lang{margin-left:44px;display:flex;align-items:center;gap:6px}
.flag{width:18px;height:11px;background:linear-gradient(135deg,#1f3c8c 0 35%,#c8102e 35% 65%,#1f3c8c 65%)}
.chev-round{width:12px;height:12px;border-radius:50%;background:var(--white);display:flex;align-items:center;justify-content:center}
.topbar .social{margin-left:42px;display:flex;gap:20px}
.dot{width:8px;height:8px;border-radius:50%;background:var(--ink)}

/* nav */
.nav{left:128px;top:44px;width:944px;height:73px;background:var(--white);border-radius:10px;display:flex;align-items:center;padding:0 28px;box-shadow:0 4px 18px rgba(10,118,189,.06)}
.brand{display:flex;align-items:center;gap:8px;font-family:"Barlow",sans-serif;font-weight:700;font-size:20px;color:var(--blue)}
.brand .mark{width:12px;height:12px;border-radius:50%;background:var(--sky)}
.nav ul{list-style:none;display:flex;gap:26px;margin-left:auto;font-size:12px;color:var(--ink)}
.btn{display:inline-flex;align-items:center;justify-content:center;background:var(--blue);color:var(--white);border-radius:22px;font-weight:500;font-size:12px}
.nav .btn{width:131px;height:34px;margin-left:24px}

/* hero */
.hero-title{left:155px;top:196px;font-size:37px;font-weight:700;line-height:50px}
.hero-text{left:156px;top:300px;width:436px;font-size:11.3px;line-height:21.2px}
.hero-photo{left:631px;top:160px;width:413px;height:284px;border-radius:14px;background:var(--white);padding:5px}
.hero-photo .fill{width:100%;height:100%;border-radius:10px;background:linear-gradient(135deg,#b9c0c6 0%,#e4e7ea 40%,#5a6067 70%,#cfd4d8 100%)}

/* section heading */
.kicker{left:0;top:500px;width:1200px;text-align:center;font-size:15px;color:var(--ink)}
.sec-title{left:0;top:528px;width:1200px;text-align:center;font-size:37px;font-weight:700}

/* form */
.form{left:268px;width:662px}
.group-title{font-size:15px;font-weight:600}
.grid{display:grid;grid-template-columns:312px 312px;column-gap:38px;row-gap:16px;margin-top:20px}
.field label{display:block;font-family:"Barlow",sans-serif;font-weight:600;font-size:13px;color:var(--ink);margin-bottom:7px}
.input{height:43px;border:1px solid var(--line);border-radius:22px;background:var(--white);display:flex;align-items:center;justify-content:space-between;padding:0 16px 0 18px;font-size:11.5px;color:var(--text)}
.textarea{height:147px;border:1px solid var(--line);border-radius:14px;background:var(--white);display:flex;justify-content:space-between;padding:18px 14px 0 18px;font-size:11.5px}
.upload{width:127px;height:127px;border:1px solid var(--line);border-radius:8px;background:var(--white);display:flex;align-items:center;justify-content:center}
.consent{display:flex;gap:14px;font-size:9.5px;line-height:21px;width:640px}
.checkbox{flex:none;width:17px;height:17px;border:1px solid var(--line);border-radius:3px;background:var(--white);margin-top:3px}
.send{width:144px;height:37px;font-size:11.5px}

/* cta */
.cta{left:128px;top:1820px;width:944px;height:132px;background:var(--blue);border-radius:10px;padding:36px 34px;color:var(--white);display:flex;align-items:center;justify-content:space-between}
.cta p{font-size:15px}
.cta h2{color:var(--white);font-size:36px;line-height:38px}
.cta .btn-light{width:156px;height:37px;border-radius:20px;background:var(--white);color:var(--ink);font-size:11.5px;font-weight:500;display:flex;align-items:center;justify-content:center}

/* footer */
.footer{left:0;top:1998px;width:1200px;height:208px}
.fcol{position:absolute;top:0}
.fcol h4{font-size:14px;font-weight:600;margin:22px 0 18px}
.fcol ul{list-style:none;font-size:10px;color:var(--ink);line-height:24.5px}
.fcontact{font-size:10px;color:var(--ink);line-height:24px;margin-top:20px}
.fcontact div{display:flex;align-items:center;gap:7px}
.fsocial{display:flex;gap:26px;margin-top:10px}
.news p{font-size:10px;line-height:18.5px;width:224px}
.news .email{margin-top:17px;width:224px;height:32px;border:1px solid var(--blue);border-radius:16px;display:flex;align-items:center;justify-content:space-between;padding:0 2px 0 16px;font-size:8.5px;color:var(--text)}
.news .go{width:28px;height:28px;border-radius:50%;background:var(--blue);display:flex;align-items:center;justify-content:center}
.bottom{left:0;top:2206px;width:1200px;height:51px;background:var(--navy);color:var(--white);font-size:10px;display:flex;align-items:center;padding:0 156px}
.bottom nav{margin-left:auto;display:flex;gap:36px}
</style>
</head>
<body>
<div class="page">

  <div class="abs topbar">
    <div class="contact">
      <span class="item"><svg width="13" height="10" viewBox="0 0 13 10"><rect x=".5" y=".5" width="12" height="9" fill="none" stroke="#27a9e1"/><path d="M.5 .5l6 5 6-5" fill="none" stroke="#27a9e1"/></svg>info@lumavex.de</span>
      <span class="item"><svg width="12" height="12" viewBox="0 0 24 24"><path d="M5 3h4l2 5-3 2a11 11 0 006 6l2-3 5 2v4a2 2 0 01-2 2A17 17 0 013 5a2 2 0 012-2z" fill="none" stroke="#27a9e1" stroke-width="2"/></svg>+49 4000 555 120-0</span>
    </div>
    <div class="links"><span>Pick Up Order</span><span>About US</span><span>Contact Us</span></div>
    <div class="lang"><span class="flag"></span><span class="chev-round"><svg width="6" height="4" viewBox="0 0 6 4"><path d="M.5.5l2.5 2.5L5.5.5" fill="none" stroke="#333" /></svg></span></div>
    <div class="social"><span class="dot"></span><span class="dot"></span><span class="dot"></span><span class="dot"></span></div>
  </div>

  <header class="abs nav">
    <div class="brand"><span class="mark"></span>Lumavex</div>
    <ul><li>Home</li><li>Endoscope Repair</li><li>Used Endoscopes</li><li>Endoscopy Systems</li><li>Endoscopy Accessories</li></ul>
    <a class="btn">Purchase Now!</a>
  </header>

  <h1 class="abs hero-title">Do You Want to Sell<br><span class="accent">Your Endoscope?</span></h1>
  <p class="abs hero-text">We are always interested in buying used endoscopes, accessories and peripherals from Olvira, Pentrix and Fujova at fair conditions. We can promise you an objective offer with a clear conscience! Use the form below to offer us your device! If you want to have several devices checked, one of our technicians will usually come to you for the check. We also check defective and incomplete devices!</p>
  <div class="abs hero-photo"><div class="fill" role="img" aria-label="Photo of a used flexible endoscope with its light connector on a white table"></div></div>

  <p class="abs kicker">Lorum Ipsum Dolor</p>
  <h2 class="abs sec-title">Sed Perspiciatis <span class="accent">Unde Omnis</span></h2>

  <section class="abs form" style="top:618px">
    <h3 class="group-title">Personal Informations</h3>
    <div class="grid">
      <div class="field"><label>Salutation</label><div class="input">Select salutation<svg width="10" height="6" viewBox="0 0 10 6"><path d="M1 1l4 4 4-4" fill="none" stroke="#0a76bd" stroke-width="1.8"/></svg></div></div>
      <div class="field"><label>co. / dr. off.</label><div class="input">Company / doctors office<svg width="10" height="6" viewBox="0 0 10 6"><path d="M1 1l4 4 4-4" fill="none" stroke="#0a76bd" stroke-width="1.8"/></svg></div></div>
      <div class="field"><label>Surname</label><div class="input">Enter surname<svg width="12" height="13" viewBox="0 0 12 13"><circle cx="6" cy="3.5" r="3" fill="#0a76bd"/><path d="M0 13a6 6 0 0112 0z" fill="#0a76bd"/></svg></div></div>
      <div class="field"><label>First Name</label><div class="input">Enter first name<svg width="12" height="13" viewBox="0 0 12 13"><circle cx="6" cy="3.5" r="3" fill="#0a76bd"/><path d="M0 13a6 6 0 0112 0z" fill="#0a76bd"/></svg></div></div>
      <div class="field"><label>Email Address</label><div class="input">Enter email<svg width="13" height="10" viewBox="0 0 13 10"><rect x=".7" y=".7" width="11.6" height="8.6" rx="1" fill="none" stroke="#0a76bd" stroke-width="1.3"/><path d="M1 1.2l5.5 4.3L12 1.2" fill="none" stroke="#0a76bd" stroke-width="1.3"/></svg></div></div>
      <div class="field"><label>Contact Number</label><div class="input">Enter phone number<svg width="13" height="13" viewBox="0 0 24 24"><path d="M5 3h4l2 5-3 2a11 11 0 006 6l2-3 5 2v4a2 2 0 01-2 2A17 17 0 013 5a2 2 0 012-2z" fill="none" stroke="#0a76bd" stroke-width="2"/></svg></div></div>
    </div>
  </section>

  <section class="abs form" style="top:935px">
    <h3 class="group-title">Informations About The Device</h3>
    <div class="grid">
      <div class="field"><label>Brand</label><div class="input">Select brand<svg width="10" height="6" viewBox="0 0 10 6"><path d="M1 1l4 4 4-4" fill="none" stroke="#0a76bd" stroke-width="1.8"/></svg></div></div>
      <div class="field"><label>Model</label><div class="input">Select model<svg width="10" height="6" viewBox="0 0 10 6"><path d="M1 1l4 4 4-4" fill="none" stroke="#0a76bd" stroke-width="1.8"/></svg></div></div>
      <div class="field"><label>Defects / Damage</label><div class="input">Write here<svg width="12" height="12" viewBox="0 0 24 24"><path d="M11 4H4v16h16v-7" fill="none" stroke="#0a76bd" stroke-width="2.2"/><path d="M18 2l4 4-10 10H8v-4z" fill="none" stroke="#0a76bd" stroke-width="2.2"/></svg></div></div>
      <div class="field"><label>Asking Price</label><div class="input">Enter here<svg width="13" height="13" viewBox="0 0 24 24"><path d="M13 2h9v9L11 22 2 13z" fill="#0a76bd"/><circle cx="17" cy="7" r="2" fill="#fff"/></svg></div></div>
    </div>
  </section>

  <section class="abs form" style="top:1170px">
    <h3 class="group-title">Remarks &amp; Picture</h3>
    <div class="field" style="margin-top:20px"><label>Remark</label><div class="textarea">Type here<svg width="13" height="13" viewBox="0 0 24 24"><path d="M11 4H4v16h16v-7" fill="none" stroke="#0a76bd" stroke-width="2.2"/><path d="M18 2l4 4-10 10H8v-4z" fill="none" stroke="#0a76bd" stroke-width="2.2"/></svg></div></div>
    <div class="field" style="margin-top:18px"><label>Upload Images</label>
      <div class="upload"><svg width="54" height="44" viewBox="0 0 54 44"><path d="M4 10h12l4-7h14l4 7h12a3 3 0 013 3v26a3 3 0 01-3 3H4a3 3 0 01-3-3V13a3 3 0 013-3z" fill="none" stroke="#0a76bd" stroke-width="2"/><circle cx="27" cy="25" r="9" fill="none" stroke="#0a76bd" stroke-width="2"/></svg></div>
    </div>
    <div class="consent" style="margin-top:26px"><span class="checkbox"></span><p>I have read the privacy policy and accept it. I agree above input will be transmitted to Lumavex GmbH to get in contact with me respectively to process my request and store all needed informations. Neither a transfer to third parties will happen, nor a use for advertising purposes by Lumavex GmbH!</p></div>
    <a class="btn send" style="margin-top:36px">Send Now</a>
  </section>

  <section class="abs cta">
    <div><p>Get In Touch</p><h2>How Can We Help You?</h2></div>
    <a class="btn-light">Contact Us Now</a>
  </section>

  <footer class="abs footer">
    <div class="fcol" style="left:156px">
      <div class="brand" style="margin-top:20px"><span class="mark"></span>Lumavex</div>
      <div class="fcontact" style="margin-top:30px">
        <div><svg width="10" height="10" viewBox="0 0 24 24"><path d="M5 3h4l2 5-3 2a11 11 0 006 6l2-3 5 2v4a2 2 0 01-2 2A17 17 0 013 5a2 2 0 012-2z" fill="#333a40"/></svg>+49 4000 555 120-0</div>
        <div><svg width="10" height="8" viewBox="0 0 13 10"><rect width="13" height="10" fill="#333a40"/><path d="M0 0l6.5 5L13 0" fill="none" stroke="#fff"/></svg>info@lumavex.de</div>
      </div>
      <div class="fsocial"><span class="dot"></span><span class="dot"></span><span class="dot"></span><span class="dot"></span></div>
    </div>
    <div class="fcol" style="left:430px"><h4>Quick Links</h4><ul><li>Home</li><li>Endoscope Repair</li><li>Used Endoscopes</li><li>Endoscopy Systems</li><li>Endoscopy Accessories</li></ul></div>
    <div class="fcol" style="left:661px"><h4>Usefull Links</h4><ul><li>Information</li><li>About Us</li><li>Contact Us</li><li>TOS</li><li>FAQ</li></ul></div>
    <div class="fcol news" style="left:820px"><h4>Newsletter</h4>
      <p>Lorem ipsum dolor sit consectetur adipiscing elit sed do eiusmod tempor incididunt ut labore et dolore magna aliqua.</p>
      <div class="email">Your Email<span class="go"><svg width="12" height="12" viewBox="0 0 24 24"><path d="M22 2L2 10l8 3 3 8z M22 2L10 13" fill="none" stroke="#fff" stroke-width="2"/></svg></span></div>
    </div>
  </footer>

  <div class="abs bottom"><span>2022 All rights reserved</span><nav><span>Privacy Policy</span><span>Terms &amp; Conditions</span></nav></div>
</div>
</body>
</html>
```